Business Card Design needed for start up company Halvora

In need of a new business card designed for a start up company based in Sydney, Halvora is a new start up innovative Company, our mission it to make property accessible for everyday Australian and to become the leading Real Estate platform in Australia. We want it to be fresh and clean.

Industry/Entity Type

Financial

Contact Information for Business Card

Section for Name
Section for Title

HALVORA - The Strength of Pooling
Mobile:
Direct:

Font styles to use
Sans Serif

Colors
33a6d7
0692cd
0255a3
ffffff

Requirements
Must have
• Logo, all business card details

```html
<!DOCTYPE html>
<html lang="en">
<head>
<meta charset="utf-8">
<title>Halvora Business Card</title>
<link href="https://fonts.googleapis.com/css2?family=Open+Sans:wght@400;600;700;800&display=swap" rel="stylesheet">
<style>
  :root {
    --sky: #33a6d7;
    --ocean: #0692cd;
    --navy: #0255a3;
    --white: #ffffff;
    --ink: #3d4750;
    --muted: #8a949c;
    --backdrop: #e8e5e0;
  }
  * { margin: 0; padding: 0; box-sizing: border-box; }
  html, body { width: 1200px; height: 1023px; overflow: hidden; }
  body {
    background: var(--backdrop);
    font-family: "Open Sans", Arial, sans-serif;
    display: flex;
    flex-direction: column;
    align-items: center;
    justify-content: center;
    gap: 48px;
  }
  .card {
    position: relative;
    width: 760px;
    height: 434px;
    border-radius: 18px;
    overflow: hidden;
    box-shadow: 0 8px 22px rgba(0,0,0,0.18);
  }

  /* Front */
  .card-front {
    background: linear-gradient(160deg, #ffffff 0%, #f2f3f4 60%, #e6e8ea 100%);
  }
  .edge-bands { position: absolute; top: 0; right: 0; width: 90px; height: 100%; }
  .front-logo {
    position: absolute;
    left: 44px;
    top: 50%;
    transform: translateY(-50%);
    display: flex;
    align-items: center;
    gap: 12px;
  }
  .logo-dot { border-radius: 50%; flex: none; }
  .front-logo .logo-dot { width: 44px; height: 44px; background: var(--sky); }
  .front-logo .logo-name {
    font-weight: 800;
    font-size: 48px;
    letter-spacing: -1px;
    color: var(--navy);
    line-height: 1;
    white-space: nowrap;
  }
  .divider {
    position: absolute;
    left: 392px;
    top: 120px;
    width: 1px;
    height: 196px;
    background: var(--navy);
    opacity: 0.7;
  }
  .identity {
    position: absolute;
    left: 418px;
    top: 96px;
  }
  .person-name {
    font-weight: 700;
    font-size: 40px;
    color: var(--sky);
    line-height: 1.1;
    white-space: nowrap;
  }
  .person-title {
    font-size: 17px;
    color: var(--muted);
    margin: 2px 0 22px 4px;
  }
  .contact-list { list-style: none; margin-left: 4px; }
  .contact-list li {
    display: flex;
    align-items: center;
    gap: 12px;
    font-size: 15px;
    color: var(--ink);
    height: 28px;
    white-space: nowrap;
  }
  .contact-list svg { width: 16px; height: 16px; flex: none; }

  /* Back */
  .card-back {
    background: radial-gradient(ellipse at 75% 30%, #35c2e2 0%, #25acd8 45%, var(--ocean) 100%);
  }
  .back-logo {
    position: absolute;
    left: 0; right: 0;
    top: 124px;
    display: flex;
    align-items: center;
    justify-content: center;
    gap: 20px;
  }
  .back-logo .logo-dot { width: 110px; height: 110px; background: var(--white); }
  .back-logo .logo-name {
    font-weight: 800;
    font-size: 96px;
    letter-spacing: -2px;
    color: var(--navy);
    line-height: 1;
    white-space: nowrap;
  }
  .tagline {
    position: absolute;
    left: 0; right: 0;
    top: 300px;
    display: flex;
    align-items: center;
    justify-content: center;
    gap: 14px;
    color: var(--white);
    font-size: 20px;
    letter-spacing: 0.5px;
  }
  .tagline .rule { width: 28px; height: 2px; background: var(--white); }
</style>
</head>
<body>

  <section class="card card-front" aria-label="Card front">
    <svg class="edge-bands" viewBox="0 0 90 434" preserveAspectRatio="none" aria-hidden="true">
      <polygon points="30,0 90,0 90,434 30,434" fill="#33a6d7"/>
      <polygon points="30,0 90,0 90,150 30,178" fill="#0255a3"/>
      <polygon points="30,178 90,150 90,160 30,188" fill="#ffffff"/>
      <rect x="30" y="0" width="6" height="434" fill="#0692cd" opacity="0.6"/>
    </svg>

    <div class="front-logo">
      <span class="logo-dot"></span>
      <span class="logo-name">HALVORA</span>
    </div>

    <div class="divider"></div>

    <div class="identity">
      <p class="person-name">Your Name</p>
      <p class="person-title">Title</p>
      <ul class="contact-list">
        <li>
          <svg viewBox="0 0 16 16"><circle cx="8" cy="8" r="7" fill="none" stroke="#33a6d7" stroke-width="1.3"/><path d="M5.5 4.5l1.5 1.5-1 1a5 5 0 0 0 3 3l1-1 1.5 1.5-1 1c-3 0-6-3-6-6z" fill="#33a6d7"/></svg>
          02-8123-4567
        </li>
        <li>
          <svg viewBox="0 0 16 16"><rect x="2" y="3" width="12" height="10" fill="none" stroke="#8a949c" stroke-width="1.3"/></svg>
          02-8123-4568
        </li>
        <li>
          <svg viewBox="0 0 16 16"><rect x="1.5" y="3.5" width="13" height="9" fill="#0692cd"/><path d="M1.5 3.5l6.5 5 6.5-5" fill="none" stroke="#ffffff" stroke-width="1.2"/></svg>
          hello@halvora.com.au
        </li>
        <li>
          <svg viewBox="0 0 16 16"><circle cx="8" cy="8" r="6.5" fill="none" stroke="#0692cd" stroke-width="1.2"/><ellipse cx="8" cy="8" rx="3" ry="6.5" fill="none" stroke="#0692cd" stroke-width="1"/><path d="M1.5 8h13M2.5 5h11M2.5 11h11" stroke="#0692cd" stroke-width="1"/></svg>
          www.halvora.com.au
        </li>
      </ul>
    </div>
  </section>

  <section class="card card-back" aria-label="Card back">
    <div class="back-logo">
      <span class="logo-dot"></span>
      <span class="logo-name">HALVORA</span>
    </div>
    <p class="tagline"><span class="rule"></span>The Strength of Pooling<span class="rule"></span></p>
  </section>

</body>
</html>
```